Life Coaching business needs a new flyer

We are an Australian business that specialises in Life Coaching, Career Coaching, Health and Wellness Coaching, Yoga and Pilates. We need a A4 double sided flyer that is full colour and folded to DL format. I have attached a couple of designs that I like and some pictures and would like the flyer to be bright yet stylish.

Industry/Entity Type

Life Coaching

```html
<!DOCTYPE html>
<html lang="en">
<head>
<meta charset="utf-8">
<title>Brightpath Coaching &amp; Meditation Studio – DL Brochure</title>
<link href="https://fonts.googleapis.com/css2?family=Open+Sans:wght@400;600;700&family=Crimson+Text:wght@600;700&family=Great+Vibes&display=swap" rel="stylesheet">
<style>
:root{
  --bg:#c9c9c9;
  --paper:#ffffff;
  --paper-grey:#f1f1f1;
  --ink:#2b2b2b;
  --blue:#1c6fb8;
  --blue-deep:#0f4f93;
  --sky:#9cc8ec;
  --teal:#1597bd;
  --teal-band:#1a8aaa;
  --green:#55b02e;
  --green-dark:#3f9320;
  --tick:#5bb531;
}
*{box-sizing:border-box;margin:0;padding:0}
html,body{width:1034px;height:1200px;overflow:hidden;background:var(--bg);font-family:"Open Sans",Arial,sans-serif;color:var(--ink)}
.sheet{position:absolute;left:97px;width:840px;height:560px;display:flex;box-shadow:0 6px 18px rgba(0,0,0,.25);background:var(--paper)}
.sheet--outside{top:25px}
.sheet--inside{top:615px}
.panel{position:relative;width:280px;height:560px;overflow:hidden;background:var(--paper)}
.panel + .panel{border-left:1px solid #e2e2e2}
.photo{position:absolute;left:0;right:0}
.body-text{font-size:7.6px;line-height:1.38;text-align:justify}
.body-text p{margin-bottom:6px}
.heading{font-family:"Crimson Text",Georgia,serif;font-weight:700;color:var(--teal);line-height:1.05}
.brand{display:flex;align-items:center;gap:6px;font-family:"Open Sans",Arial,sans-serif;font-weight:700}
.brand-dot{width:14px;height:14px;border-radius:50%}

/* outside: testimonials */
.testimonials .photo{top:0;height:175px;background:linear-gradient(180deg,#3f86d1 0%,#8ec0ec 55%,#ffffff 100%)}
.testimonials .heading{position:absolute;top:178px;left:20px;font-size:17px}
.testimonials .body-text{position:absolute;top:204px;left:20px;right:20px}

/* outside: contact */
.contact{background:var(--paper-grey)}
.contact .intro{position:absolute;top:28px;left:24px;right:24px;font-size:7.4px;line-height:1.4}
.contact .intro p{margin-bottom:8px}
.contact .brand{position:absolute;top:120px;left:0;right:0;justify-content:center;color:var(--blue);font-size:13px}
.contact .brand-dot{background:var(--green)}
.contact-list{position:absolute;top:160px;left:0;right:0;text-align:center;font-size:8.6px;line-height:1.45}
.contact-list .heading{font-size:17px;color:var(--blue-deep);margin-bottom:3px}
.contact-list .web{font-weight:700;color:var(--blue-deep)}
.offer-band{position:absolute;top:252px;left:0;right:0;height:62px;background:var(--teal-band);color:#fff;text-align:center;font-family:"Crimson Text",Georgia,serif;font-weight:600;font-size:10px;line-height:1.3;padding-top:11px}
.contact .photo{top:314px;bottom:0;background:linear-gradient(180deg,#7a6a4a 0%,#3a3028 55%,#1e1a18 100%)}

/* outside: cover */
.cover{background:var(--paper)}
.cover .sky{top:0;height:200px;background:linear-gradient(180deg,var(--blue-deep) 0%,var(--blue) 45%,var(--sky) 100%)}
.cover .brand{position:absolute;top:58px;left:0;right:0;justify-content:center;color:#fff;font-size:15px}
.cover .brand-dot{background:#fff}
.cover .scene{top:200px;bottom:0;background:linear-gradient(180deg,#a9cde6 0%,#8fb96a 35%,#5f9a33 70%,#4f8a2a 100%)}
.cover-arc{position:absolute;left:0;bottom:0;width:280px;height:230px}
.cover-title{position:absolute;left:0;right:0;bottom:40px;text-align:center;font-family:"Great Vibes",cursive;color:#fff;font-size:28px;line-height:1.15}

/* inside: intro */
.intro-panel .photo{top:0;height:190px;background:linear-gradient(180deg,#2b76c0 0%,#7db5e4 55%,#e9f2fa 100%)}
.intro-panel .brand{position:absolute;top:24px;left:28px;color:#fff;font-size:13px}
.intro-panel .brand-dot{background:#fff}
.questions{position:absolute;top:200px;left:24px;right:22px;font-size:8.4px;font-weight:700;line-height:1.35}
.questions p{margin-bottom:6px}
.intro-panel .heading{position:absolute;top:300px;left:24px;right:20px;font-size:17px}
.intro-panel .body-text{position:absolute;top:344px;left:24px;right:22px;font-size:8.2px}
.intro-panel .body-text p{margin-bottom:9px}

/* inside: services */
.services .photo{top:0;height:170px;background:linear-gradient(180deg,#5fa9df 0%,#b9d7c2 55%,#ffffff 100%)}
.services .content{position:absolute;top:160px;left:22px;right:22px}
.services .heading{font-size:15px;margin:8px 0 3px}

/* inside: help */
.help .photo{top:0;height:160px;background:linear-gradient(180deg,#f2c27a 0%,#d9a46a 45%,#bfd39a 80%,#ffffff 100%)}
.help .content{position:absolute;top:160px;left:22px;right:22px}
.help .heading{font-size:15px;margin:8px 0 3px}
.tick-list{list-style:none;margin:6px 0 4px 2px;font-size:7.6px;font-style:italic;line-height:1.5}
.tick-list li{display:flex;align-items:center;gap:5px}
.tick-list svg{flex:none}
</style>
</head>
<body>

<section class="sheet sheet--outside" aria-label="Brochure outside">
  <article class="panel testimonials">
    <div class="photo" role="img" aria-label="Photo of four happy friends jumping against a blue sky"></div>
    <h2 class="heading">Happy Clients Testimonials</h2>
    <div class="body-text">
      <p>“I have lost 10 kilos and now have the energy to play with my kids. Thanks Anna for you support/guidance and helping me get rid of my limiting beliefs. I feel I can achieve anything now! The sky’s the limit” Leah, Manly</p>
      <p>“I had always wanted to start up own café however every time it came to putting it into practice I would procrastinate and not achieve anything. I became overwhelmed with the whole process and never achieved anything. Anna put it into bite sized chunks and helped me to set small achievable goals. I am now a happy café owner.” Nora, Bondi</p>
      <p>“Anna has helped to change my life around in all aspects. I would have been lost without her. Thanks Anna for your professionalism, support and guidance.” Bella, Neutral Bay</p>
      <p>“I was so busy with kids, work, and my husband I lost who I was. Anna has helped me find the person I am again.” Sophie, Ryde</p>
      <p>“When I started with Coach Anna, I didn’t know anything about coaching. I called her because she helped a friend of mine make a career change that was a perfect fit for her. I had the opportunity to make a change too and did not know where to start. I am now in a job that I love. I would recommend Anna to everyone.” Jacob, Ohio USA</p>
    </div>
  </article>

  <article class="panel contact">
    <div class="intro">
      <p>Brightpath Coaching &amp; Meditation Studio is a professional service that can help you achieve the goals that you are looking for in Life Coaching, Meditation, and Yoga/Pilates.</p>
      <p>If you are ready to take your life to the next level and would like to know more, please</p>
    </div>
    <div class="brand"><span class="brand-dot"></span>Brightpath</div>
    <div class="contact-list">
      <h3 class="heading">contact us.</h3>
      <p><strong>Phone :</strong> 02 9000 4417</p>
      <p>hello@brightpathstudio.com.au</p>
      <p class="web">www.brightpathstudio.com.au</p>
    </div>
    <div class="offer-band">Free Introductory Life Coaching<br>Phone/Video Call session - 20 mins<br>(To see if coaching is right for you)</div>
    <div class="photo" role="img" aria-label="Portrait photo of the two coaches"></div>
  </article>

  <article class="panel cover">
    <div class="photo sky" role="img" aria-label="Bright blue sky"></div>
    <div class="brand"><span class="brand-dot"></span>Brightpath</div>
    <div class="photo scene" role="img" aria-label="Photo of a group meditating on mats on a grassy lawn"></div>
    <svg class="cover-arc" viewBox="0 0 280 230" aria-hidden="true">
      <defs>
        <radialGradient id="arcGreen" cx="50%" cy="30%" r="80%">
          <stop offset="0" stop-color="#7ccb45"/>
          <stop offset="1" stop-color="#3f9320"/>
        </radialGradient>
      </defs>
      <path d="M0 230 L0 120 Q140 -10 280 40 L280 230 Z" fill="url(#arcGreen)"/>
    </svg>
    <div class="cover-title">Life Coaching<br>Meditation<br>Yoga/Pilates</div>
  </article>
</section>

<section class="sheet sheet--inside" aria-label="Brochure inside">
  <article class="panel intro-panel">
    <div class="photo" role="img" aria-label="Photo of a smiling older couple on a sailing boat"></div>
    <div class="brand"><span class="brand-dot"></span>Brightpath</div>
    <div class="questions">
      <p>Are you looking at making changes this year?</p>
      <p>Are you stuck in a rut or at a crossroad in your life?</p>
      <p>Are you wanting to lose weigh but can’t get motivated?</p>
      <p>Do you have ongoing problems with your career, relationships, or just life itself?<br>Life coaching is the answer</p>
    </div>
    <h2 class="heading">Brightpath Coaching &amp; Meditation Studio</h2>
    <div class="body-text">
      <p>Our mission is to help you become the best possible person you can be. Mentally, physically, and spiritually.</p>
      <p>We offer highly qualified and compassionate trainers/coaches for Life Coaching, Meditation, Yoga and Pilates.</p>
      <p>They will guide and motivate you every step of the way to achieve all your dreams and goals.</p>
      <p>They will make you be the best you can be.</p>
    </div>
  </article>

  <article class="panel services">
    <div class="photo" role="img" aria-label="Photo of a joyful woman raising her arm under palm trees"></div>
    <div class="content body-text">
      <h2 class="heading">Life Coaching</h2>
      <p>Your Life Coach will give you the confidence and the ability to move forward in a positive manner in all areas of your life where you crave change.</p>
      <p>Life Coaching is about breaking down the barriers preventing this change from happening, and creating the ideal environment for positive action to take place. It is a holistic approach, which looks at the present and sets goals for a totally successful future.</p>
      <h2 class="heading">Career Coaching</h2>
      <p>Are you at a crossroads in your career and at a loss about what to do next? Do you want your work to be in alignment with the authentic you? It can be difficult to assess career options, goals, and strategies, and have the confidence to implement changes on your own. With the right coaching support, you will gain the clarity that you need to take control and have a fulfilling and rewarding career.</p>
      <h2 class="heading">Wellness Coaching</h2>
      <p>Health and wellness coaches help their clients find the motivation and tools to achieve their health and wellness goals, working with the client to examine and improve the psychological framework that supports those goals.</p>
    </div>
  </article>

  <article class="panel help">
    <div class="photo" role="img" aria-label="Photo of a mother hugging her young daughter in sunlight"></div>
    <div class="content body-text">
      <h2 class="heading">Why Would I Need Help?</h2>
      <p>Coaching is for anyone who wants to make lasting changes in their life.<br>Coaching can assist with such issues as:</p>
      <ul class="tick-list">
        <li><svg width="8" height="8" viewBox="0 0 10 10"><circle cx="5" cy="5" r="5" fill="var(--tick)"/><path d="M2.5 5.2 L4.3 7 L7.6 3.2" stroke="#fff" stroke-width="1.4" fill="none"/></svg>Creating a better work- life balance</li>
        <li><svg width="8" height="8" viewBox="0 0 10 10"><circle cx="5" cy="5" r="5" fill="var(--tick)"/><path d="M2.5 5.2 L4.3 7 L7.6 3.2" stroke="#fff" stroke-width="1.4" fill="none"/></svg>Resolving relationship issues</li>
        <li><svg width="8" height="8" viewBox="0 0 10 10"><circle cx="5" cy="5" r="5" fill="var(--tick)"/><path d="M2.5 5.2 L4.3 7 L7.6 3.2" stroke="#fff" stroke-width="1.4" fill="none"/></svg>Career guidance</li>
        <li><svg width="8" height="8" viewBox="0 0 10 10"><circle cx="5" cy="5" r="5" fill="var(--tick)"/><path d="M2.5 5.2 L4.3 7 L7.6 3.2" stroke="#fff" stroke-width="1.4" fill="none"/></svg>Stress management</li>
        <li><svg width="8" height="8" viewBox="0 0 10 10"><circle cx="5" cy="5" r="5" fill="var(--tick)"/><path d="M2.5 5.2 L4.3 7 L7.6 3.2" stroke="#fff" stroke-width="1.4" fill="none"/></svg>Weight loss and fitness</li>
        <li><svg width="8" height="8" viewBox="0 0 10 10"><circle cx="5" cy="5" r="5" fill="var(--tick)"/><path d="M2.5 5.2 L4.3 7 L7.6 3.2" stroke="#fff" stroke-width="1.4" fill="none"/></svg>Motivation and goal setting</li>
        <li><svg width="8" height="8" viewBox="0 0 10 10"><circle cx="5" cy="5" r="5" fill="var(--tick)"/><path d="M2.5 5.2 L4.3 7 L7.6 3.2" stroke="#fff" stroke-width="1.4" fill="none"/></svg>Boosting your self esteem</li>
        <li><svg width="8" height="8" viewBox="0 0 10 10"><circle cx="5" cy="5" r="5" fill="var(--tick)"/><path d="M2.5 5.2 L4.3 7 L7.6 3.2" stroke="#fff" stroke-width="1.4" fill="none"/></svg>Overcoming negative emotions and thoughts</li>
        <li><svg width="8" height="8" viewBox="0 0 10 10"><circle cx="5" cy="5" r="5" fill="var(--tick)"/><path d="M2.5 5.2 L4.3 7 L7.6 3.2" stroke="#fff" stroke-width="1.4" fill="none"/></svg>Better time management</li>
      </ul>
      <h2 class="heading">Meditation</h2>
      <p>We specialise in teaching meditation from beginners to advanced and teach a variety of techniques for stress reduction, peace of mind, stillness, and clarity.</p>
      <h2 class="heading">Yoga/Pilates</h2>
      <p>Your highly qualified and experienced Yoga or Pilates instructor will come to you and create a fun and varied workout based on what you enjoy and what your goals are.</p>
    </div>
  </article>
</section>

</body>
</html>
```